KORVEL Group Pty Ltd. Website and Domain

www.korvelgroup.com.au

require email addresses setup.

Info@korvelgroup.com.au
accounts@korvelgroup.com.au
peter.halloway@korvelgroup.com.au
grant.whitley@korvelgroup.com.au

Website should promote commercial and domestic electrical services, audio visual services and data and fibre installations.

similar to my mates site www.brisvane.com.au

Website needs to promote professionalism, electrical/electrician, audio visual and data/fibre cabling installations.

promote environmental friendly imaginary.

Coding

```html
<!DOCTYPE html>
<html lang="en">
<head>
<meta charset="utf-8">
<title>KORVEL Group – Electrical, Audio Visual &amp; Data</title>
<link href="https://fonts.googleapis.com/css2?family=Open+Sans:wght@600&family=Poppins:wght@400;500;600&family=Roboto:wght@300;400;500;700&family=Lato:wght@400&display=swap" rel="stylesheet">
<style>
:root{
  --green:#a6ce39;
  --blue:#29a3dc;
  --navy:#0e1630;
  --footer:#0b1330;
  --ink:#333a44;
  --muted:#5f6670;
  --body:#4a5f7a;
  --white:#ffffff;
  --line:#e3e6ea;
}
*{margin:0;padding:0;box-sizing:border-box}
html,body{width:1200px;height:3891px;overflow:hidden}
body{position:relative;background:var(--white);font-family:"Poppins",sans-serif;color:var(--ink)}
.abs{position:absolute}
.accent-bar{position:absolute;width:58px;height:3px;background:linear-gradient(90deg,var(--green),var(--blue))}

/* header */
.topbar{position:absolute;left:0;top:0;width:1200px;height:91px;background:var(--white)}
.brand{position:absolute;display:flex;align-items:center;gap:12px;font-family:"Poppins",sans-serif;font-weight:600;color:var(--blue);white-space:nowrap}
.brand .dot{border-radius:50%;background:var(--green)}
.topbar .brand{left:121px;top:20px;font-size:34px;letter-spacing:1px}
.topbar .brand .dot{width:34px;height:34px}
.callus{position:absolute;left:930px;top:26px;display:flex;gap:12px;align-items:center}
.callus .txt{font-family:"Roboto",sans-serif;font-size:14px;line-height:18px;color:var(--ink);white-space:nowrap}
.callus .txt b{display:block;font-weight:400;font-size:17px}

/* hero */
.hero{position:absolute;left:0;top:91px;width:1200px;height:586px;
  background:linear-gradient(100deg,#8d8a86 0%,#6b5c55 30%,#4a4b57 55%,#2e3a5a 75%,#c9ccd2 100%)}
.hero-shade{position:absolute;inset:0;background:linear-gradient(180deg,rgba(0,0,0,.35),rgba(0,0,0,.05) 40%,rgba(0,0,0,.15))}
.nav{position:absolute;left:127px;top:22px;display:flex;align-items:center;font-family:"Roboto",sans-serif;font-size:22px;color:var(--white)}
.nav a{color:inherit;text-decoration:none;white-space:nowrap}
.nav a.active{color:var(--green);text-decoration:underline;text-underline-offset:5px}
.nav .sep{width:1px;height:22px;border-left:1px dotted rgba(255,255,255,.5);margin:0 34px}
.social{position:absolute;display:flex;gap:11px}
.social span{width:28px;height:28px;border-radius:50%;border:2px solid var(--white)}
.hero .social{left:988px;top:22px}
.hero-title{position:absolute;left:0;width:1200px;top:294px;text-align:center;font-family:"Open Sans",sans-serif;font-weight:600;font-size:51px;line-height:64px;color:var(--white)}
.arrow{position:absolute;width:40px;height:40px;border-radius:50%;display:flex;align-items:center;justify-content:center}
.arrow.prev{left:105px;top:246px;border:2px solid rgba(255,255,255,.8)}
.arrow.next{left:949px;top:246px;background:var(--blue)}
.hero-dots{position:absolute;left:512px;top:524px;display:flex;gap:9px}
.hero-dots span{width:10px;height:10px;border-radius:50%;border:1.5px solid var(--white)}
.hero-dots span.on{background:var(--green);border-color:var(--green)}

/* about */
.about{position:absolute;left:0;top:677px;width:1200px;height:632px;background:linear-gradient(180deg,#ffffff 0%,#f1f2f4 55%,#d9dce1 100%)}
.about-emblem{position:absolute;left:128px;top:120px;width:330px;height:330px;border-radius:50%;background:radial-gradient(circle,#e4f2fa 0%,#d3ebf7 55%,#e9f3d3 100%)}
.section-h{font-family:"Roboto",sans-serif;font-weight:300;font-size:41px;color:var(--ink);white-space:nowrap}
.section-h b{font-weight:500}
.about h2{position:absolute;left:582px;top:125px}
.about .accent-bar{left:582px;top:181px;width:36px}
.about p{position:absolute;left:582px;width:425px;font-family:"Lato",sans-serif;color:var(--body)}
.about .p-sm{font-size:14px;line-height:26px}
.about .p-lg{font-size:17px;line-height:27px;color:#2f3a4a}

/* why */
.why h2{position:absolute;left:0;width:1200px;text-align:center;top:1385px}
.why .accent-bar{left:571px;top:1444px}
.why-card{position:absolute;top:1485px;width:350px;height:337px;text-align:center}
.why-card.featured{background:var(--white);box-shadow:0 6px 26px rgba(0,0,0,.12)}
.why-card svg{position:absolute;left:125px;top:52px}
.why-card h3{position:absolute;left:0;width:100%;top:200px;font-family:"Roboto",sans-serif;font-weight:400;font-size:18px;color:var(--ink)}
.why-card p{position:absolute;left:20px;width:310px;top:236px;font-family:"Lato",sans-serif;font-size:14.5px;line-height:24px;color:var(--body)}

/* services */
.services{position:absolute;left:0;top:1949px;width:1200px;height:726px;background:linear-gradient(120deg,#1c2b40 0%,#102235 40%,#141d2c 70%,#2a3440 100%)}
.services-overlay{position:absolute;inset:0;background:rgba(10,18,35,.55)}
.services h2{position:absolute;left:0;width:1200px;text-align:center;top:70px;color:var(--white)}
.services .accent-bar{left:571px;top:132px}
.center-emblem{position:absolute;left:449px;top:204px;width:302px;height:302px;border-radius:50%;background:radial-gradient(circle,rgba(41,163,220,.35) 0%,rgba(41,163,220,.15) 60%,rgba(166,206,57,.25) 100%)}
.node{position:absolute;width:80px;height:80px}
.ring-dot{position:absolute;width:14px;height:14px;border-radius:50%;background:var(--white);border:2px solid var(--blue)}
.svc{position:absolute;color:var(--white)}
.svc h3{font-family:"Poppins",sans-serif;font-weight:600;font-size:20px;line-height:24px}
.svc p{margin-top:10px;font-family:"Poppins",sans-serif;font-size:14.5px;line-height:24px;width:200px}
.btn{position:absolute;display:flex;align-items:center;justify-content:center;gap:8px;background:var(--blue);color:var(--white);font-family:"Poppins",sans-serif;font-size:16px;border-radius:3px;white-space:nowrap}
.services .btn{left:521px;top:568px;width:165px;height:46px}

/* testimonials */
.reviews h2{position:absolute;left:0;width:1200px;text-align:center;top:2753px}
.reviews .accent-bar{left:571px;top:2812px}
.review{position:absolute;top:2847px;width:276px;height:263px;background:var(--white);border:1px solid var(--line);box-shadow:0 2px 10px rgba(0,0,0,.05)}
.review .stars{position:absolute;left:32px;top:26px;color:#f6a21e;font-size:17px;letter-spacing:2px}
.review .quote{position:absolute;left:32px;top:54px;font-family:"Poppins",sans-serif;font-weight:500;font-size:13.5px;color:#222;white-space:nowrap}
.review .text{position:absolute;left:32px;top:82px;width:218px;font-family:"Poppins",sans-serif;font-size:12px;line-height:20px;color:#6a6f76}
.review .avatar{position:absolute;left:34px;top:202px;width:30px;height:30px;border-radius:50%;background:#8a8d92}
.review .name{position:absolute;left:78px;top:200px;font-size:12.5px;font-weight:500;color:#222;line-height:18px}
.review .name span{display:block;font-weight:400;color:#555}
.rev-dots{position:absolute;left:564px;top:3150px;display:flex;gap:8px}
.rev-dots span{width:10px;height:10px;border-radius:50%;border:1.5px solid #9aa0a6}
.rev-dots span.on{background:var(--blue);border-color:var(--blue)}

/* cta */
.cta{position:absolute;left:0;top:3256px;width:1200px;height:197px;background:var(--green);overflow:hidden}
.cta-blob{position:absolute;left:-40px;top:0;width:406px;height:197px;background:var(--blue);border-radius:0 99px 99px 0}
.cta-globe{position:absolute;left:205px;top:46px}
.cta-text{position:absolute;left:446px;top:64px;font-family:"Poppins",sans-serif;font-size:29px;line-height:37px;color:var(--white);font-weight:400}
.cta-text b{font-weight:600}
.cta .btn{left:884px;top:79px;width:168px;height:39px;border-radius:20px;font-size:15px}

/* footer */
.footer{position:absolute;left:0;top:3483px;width:1200px;height:408px;background:var(--footer)}
.footer .brand{left:166px;top:112px;font-size:38px;color:var(--blue)}
.footer .brand .dot{width:40px;height:40px}
.footer .social{left:226px;top:214px;gap:16px}
.footer .social span{width:24px;height:24px;border-color:var(--blue)}
.foot-links{position:absolute;left:509px;top:93px;list-style:none;font-family:"Poppins",sans-serif;font-size:16px;line-height:29px;color:#d9dde6}
.field{position:absolute;background:#e8eef5;border-radius:2px;font-family:"Poppins",sans-serif;font-size:14px;color:#7b8596;padding:6px 12px}
.footer .btn{left:671px;top:276px;width:104px;height:37px;border-radius:2px;font-size:15px}
.copyright{position:absolute;left:0;top:340px;width:1200px;height:68px;border-top:1px solid #232c47;font-family:"Poppins",sans-serif;font-size:14px;color:#8a93a8}
.copyright .left{position:absolute;left:121px;top:22px}
.copyright .right{position:absolute;left:826px;top:22px}
</style>
</head>
<body>

<header class="topbar">
  <div class="brand"><span class="dot"></span>KORVEL</div>
  <div class="callus">
    <svg width="36" height="36" viewBox="0 0 24 24" fill="none" stroke="#333a44" stroke-width="1.5" stroke-linecap="round" stroke-linejoin="round"><path d="M22 16.9v3a2 2 0 0 1-2.2 2 19.8 19.8 0 0 1-8.6-3.1 19.5 19.5 0 0 1-6-6A19.8 19.8 0 0 1 2.1 4.2 2 2 0 0 1 4.1 2h3a2 2 0 0 1 2 1.7c.1.9.4 1.8.7 2.7a2 2 0 0 1-.5 2.1L8 9.8a16 16 0 0 0 6 6l1.3-1.3a2 2 0 0 1 2.1-.4c.9.3 1.8.6 2.7.7a2 2 0 0 1 1.7 2z"/><path d="M15 2a8 8 0 0 1 7 7M15 6a4 4 0 0 1 3 3"/></svg>
    <div class="txt">Call Us<b>555.014.2290</b></div>
  </div>
</header>

<section class="hero">
  <div class="abs" style="inset:0" role="img" aria-label="Photograph of an electrician stripping cable wires with a customer in the background"></div>
  <div class="hero-shade"></div>
  <nav class="nav">
    <a class="active" href="#">Home</a><span class="sep"></span>
    <a href="#">About us</a><span class="sep"></span>
    <a href="#">Services</a><span class="sep"></span>
    <a href="#">Gallery</a><span class="sep"></span>
    <a href="#">Contact</a>
  </nav>
  <div class="social"><span></span><span></span><span></span></div>
  <div class="arrow prev"><svg width="14" height="14" viewBox="0 0 14 14"><path d="M9 2 4 7l5 5" fill="none" stroke="#fff" stroke-width="2"/></svg></div>
  <div class="arrow next"><svg width="14" height="14" viewBox="0 0 14 14"><path d="m5 2 5 5-5 5" fill="none" stroke="#fff" stroke-width="2"/></svg></div>
  <h1 class="hero-title">See What We Can<br>Do For You</h1>
  <div class="hero-dots"><span></span><span class="on"></span><span></span><span></span></div>
  <svg class="abs" style="left:582px;top:510px" width="38" height="14" viewBox="0 0 38 14"><path d="M1 1l18 11L37 1" fill="none" stroke="#fff" stroke-width="1.5"/></svg>
</section>

<section class="about">
  <div class="abs" style="left:0;top:420px;width:1200px;height:212px" role="img" aria-label="Faint landscape of power pylons and transmission lines"></div>
  <div class="about-emblem" role="img" aria-label="Large company emblem"></div>
  <h2 class="section-h">About <b>Korvel</b></h2>
  <div class="accent-bar"></div>
  <p class="p-sm" style="top:201px">Lorem Ipsum is simply dummy text of the printing and typesetting industry. Lorem Ipsum has been the industry's standard</p>
  <p class="p-lg" style="top:272px">Lorem Ipsum is simply dummy text of the printing and typesetting industry.</p>
  <p class="p-sm" style="top:337px">Lorem Ipsum is simply dummy text of the printing and typesetting industry. Lorem Ipsum has been the industry's standard dummy text ever since the 1500s, when an unknown printer took a galley of type and scrambled it to make a type specimen book.</p>
</section>

<section class="why">
  <h2 class="section-h">Why <b>Choose Us</b></h2>
  <div class="accent-bar"></div>
  <div class="why-card" style="left:73px">
    <svg width="100" height="132" viewBox="0 0 100 132" fill="none"><path d="M30 8A48 48 0 0 0 30 92M70 8A48 48 0 0 1 70 92" stroke="#c9ccd1" stroke-width="5"/><line x1="50" y1="100" x2="50" y2="122" stroke="#c9ccd1" stroke-width="2"/><circle cx="50" cy="126" r="5" fill="#c9ccd1"/><circle cx="50" cy="50" r="22" stroke="#555" stroke-width="2"/></svg>
    <h3>Over 10 Years Experience</h3>
    <p>Lorem Ipsum is simply dummy text of the printing and typesetting industry.</p>
  </div>
  <div class="why-card featured" style="left:422px">
    <svg width="100" height="132" viewBox="0 0 100 132" fill="none"><path d="M30 8A48 48 0 0 0 30 92M70 8A48 48 0 0 1 70 92" stroke="#c9ccd1" stroke-width="5"/><line x1="50" y1="100" x2="50" y2="122" stroke="#c9ccd1" stroke-width="2"/><circle cx="50" cy="126" r="5" fill="#c9ccd1"/><rect x="36" y="36" width="28" height="28" stroke="#555" stroke-width="2"/></svg>
    <h3>BEST MATERIALS</h3>
    <p>Lorem Ipsum is simply dummy text of the printing and typesetting industry.</p>
  </div>
  <div class="why-card" style="left:777px">
    <svg width="100" height="132" viewBox="0 0 100 132" fill="none"><path d="M30 8A48 48 0 0 0 30 92M70 8A48 48 0 0 1 70 92" stroke="#c9ccd1" stroke-width="5"/><line x1="50" y1="100" x2="50" y2="122" stroke="#c9ccd1" stroke-width="2"/><circle cx="50" cy="126" r="5" fill="#c9ccd1"/><path d="M50 30l4 12h12l-10 8 4 12-10-8-10 8 4-12-10-8h12z" stroke="#555" stroke-width="2"/></svg>
    <h3>PROFESSIONAL STANDARDS</h3>
    <p>Lorem Ipsum is simply dummy text of the printing and typesetting industry.</p>
  </div>
</section>

<section class="services">
  <div class="abs" style="inset:0" role="img" aria-label="Blurred photograph of electrical tools, cable reels and a multimeter on a workbench"></div>
  <div class="services-overlay"></div>
  <h2 class="section-h">Our <b>Services</b></h2>
  <div class="accent-bar"></div>
  <div class="center-emblem" role="img" aria-label="Company emblem at the centre of the services diagram"></div>

  <span class="ring-dot" style="left:469px;top:249px"></span>
  <span class="ring-dot" style="left:697px;top:222px"></span>
  <span class="ring-dot" style="left:737px;top:402px"></span>
  <span class="ring-dot" style="left:469px;top:436px"></span>

  <svg class="node" style="left:371px;top:203px" viewBox="0 0 80 80"><path d="M10 62A34 34 0 0 1 22 12" fill="none" stroke="#29a3dc" stroke-width="3"/><circle cx="40" cy="40" r="28" fill="#fff" stroke="#a6ce39" stroke-width="2"/><path d="M28 52h24M30 50v-5M36 50v-8M42 50v-11M48 50v-15" stroke="#333" stroke-width="2.5"/></svg>
  <svg class="node" style="left:726px;top:172px" viewBox="0 0 80 80"><path d="M58 10A34 34 0 0 1 70 60" fill="none" stroke="#29a3dc" stroke-width="3"/><circle cx="40" cy="40" r="28" fill="#fff" stroke="#a6ce39" stroke-width="2"/><text x="40" y="38" text-anchor="middle" font-family="Poppins,sans-serif" font-size="16" fill="#333">$</text><path d="M24 50h8l6 3h14" fill="none" stroke="#333" stroke-width="2"/></svg>
  <svg class="node" style="left:768px;top:379px" viewBox="0 0 80 80"><path d="M58 10A34 34 0 0 1 70 60" fill="none" stroke="#29a3dc" stroke-width="3"/><circle cx="40" cy="40" r="28" fill="#fff" stroke="#a6ce39" stroke-width="2"/><path d="M28 30h10v20H28zM40 38h12M40 43h12M40 48h12" stroke="#333" stroke-width="2.5" fill="none"/></svg>
  <svg class="node" style="left:389px;top:450px" viewBox="0 0 80 80"><path d="M10 62A34 34 0 0 1 22 12" fill="none" stroke="#29a3dc" stroke-width="3"/><circle cx="40" cy="40" r="28" fill="#fff" stroke="#a6ce39" stroke-width="2"/><circle cx="40" cy="35" r="9" fill="none" stroke="#333" stroke-width="2"/><path d="M26 50h28" stroke="#333" stroke-width="2"/></svg>

  <div class="svc" style="left:153px;top:188px"><h3>Electrical Services</h3><p>Lorem Ipsum is simply dummy text of the printing and typesetting industry.</p></div>
  <div class="svc" style="left:834px;top:152px"><h3>Data Services</h3><p>Lorem Ipsum is simply dummy text of the printing and typesetting industry.</p></div>
  <div class="svc" style="left:873px;top:363px"><h3>Fibre Cabling<br>Installations</h3><p>Lorem Ipsum is simply dummy text of the printing and typesetting industry.</p></div>
  <div class="svc" style="left:177px;top:428px"><h3>Audio Visual<br>Services</h3><p>Lorem Ipsum is simply dummy text of the printing and typesetting industry.</p></div>

  <div class="btn">Learn More <svg width="20" height="10" viewBox="0 0 20 10"><path d="M0 5h18M14 1l4 4-4 4" fill="none" stroke="#fff" stroke-width="1.6"/></svg></div>

  <svg class="abs" style="left:0;top:666px" width="1200" height="60" viewBox="0 0 1200 60" preserveAspectRatio="none"><path d="M0 60V34Q600-18 1200 34V60z" fill="#fff"/><path d="M0 36Q600-14 1200 36" fill="none" stroke="#a6ce39" stroke-width="5"/></svg>
</section>

<section class="reviews">
  <h2 class="section-h">Our <b>Services</b></h2>
  <div class="accent-bar"></div>
  <article class="review" style="left:168px">
    <div class="stars">★★★★★</div>
    <div class="quote">"SOLID Service! Vety consistent!"</div>
    <p class="text">the printing and typesetting industry. Lorem Ipsum has been the industry's standard dummy text ever since the 1500s Lorem Ipsum!</p>
    <div class="avatar"></div>
    <div class="name">Marcus Ellery<span>Web Development</span></div>
  </article>
  <article class="review" style="left:463px">
    <div class="stars">★★★★★</div>
    <div class="quote">"SOLID Service! Vety consistent!"</div>
    <p class="text">the printing and typesetting industry. Lorem Ipsum has been the industry's standard dummy text ever since the 1500s Lorem Ipsum!</p>
    <div class="avatar"></div>
    <div class="name">Marcus Ellery<span>Web Development</span></div>
  </article>
  <article class="review" style="left:757px">
    <div class="stars">★★★★★</div>
    <div class="quote">"SOLID Service! Vety consistent!"</div>
    <p class="text">the printing and typesetting industry. Lorem Ipsum has been the industry's standard dummy text ever since the 1500s Lorem Ipsum!</p>
    <div class="avatar"></div>
    <div class="name">Marcus Ellery<span>Web Development</span></div>
  </article>
  <div class="rev-dots"><span></span><span class="on"></span><span></span><span></span></div>
</section>

<section class="cta">
  <div class="cta-blob"></div>
  <svg class="cta-globe" width="106" height="106" viewBox="0 0 106 106" fill="none" stroke="#fff" stroke-width="3"><circle cx="56" cy="50" r="34"/><ellipse cx="56" cy="50" rx="14" ry="34"/><path d="M22 50h68M27 33h58M27 67h58"/><path d="M18 24A44 44 0 0 0 40 96" stroke-width="4"/></svg>
  <div class="cta-text"><b>Contact us now</b> and we will<br>respond today!</div>
  <div class="btn">Contact Now</div>
</section>

<footer class="footer">
  <div class="brand"><span class="dot"></span>KORVEL</div>
  <div class="social"><span></span><span></span><span></span></div>
  <ul class="foot-links"><li>Home</li><li>About Us</li><li>Services</li><li>Gallery</li><li>Contact</li></ul>
  <div class="field" style="left:671px;top:83px;width:199px;height:35px">Name</div>
  <div class="field" style="left:879px;top:83px;width:201px;height:35px">Email</div>
  <div class="field" style="left:671px;top:128px;width:409px;height:35px">Subject</div>
  <div class="field" style="left:671px;top:174px;width:409px;height:92px">Message</div>
  <div class="btn">Send</div>
  <div class="copyright">
    <span class="left">Copyright 2020 Korvel. All Rights Reserved.</span>
    <span class="right">Privacy Policy &nbsp;&nbsp;|&nbsp;&nbsp; Terms Of Services</span>
  </div>
</footer>

</body>
</html>
```